Architectural, Engineering and Design Build

Tovandex4.com
Veteran Disabled Certified company is doing business in Architecture, Engineer and Design build - look simialr websites and come up with design follow following website
https://hollis-darnet.example/
https://www.venlorcogroup.example/
https://www.pembrisgc.example/contract-vehicles/service-disabled-veteran-owned-small-business-sdvosb/
https://www.corbelnetlink.example/about/sdvosb/

Target Market(s)

US - Defense and Federal Government

Industry/Entity Type

Colors
0054AA
0677BA
7BADD7
CADEEF
E8F1F8

Requirements
Must have
• Army, American patriotism , Buildings, construction, architecture, engineering
Nice to have
• I need to attract federal government agencies and Defense

```html
<!DOCTYPE html>
<html lang="en">
<head>
<meta charset="utf-8">
<title>Tovandex4 — Architecture, Engineering &amp; Design Build</title>
<link rel="stylesheet" href="https://fonts.googleapis.com/css2?family=Poppins:wght@400;500;600;700;800&display=swap">
<style>
:root{
  --red:#d7101a;
  --red-band:#c63a3c;
  --navy:#1a2363;
  --navy-deep:#1c2868;
  --ink:#2b2b33;
  --muted:#4a4a55;
  --pink:#f7e5e5;
  --teal:#3fae9a;
  --line:#e3e3e8;
  --white:#ffffff;
}
*{box-sizing:border-box;margin:0;padding:0}
html,body{width:1200px;height:3711px;overflow:hidden}
body{position:relative;font-family:"Poppins",sans-serif;color:var(--ink);background:var(--white)}
.abs{position:absolute}
a{color:inherit;text-decoration:none}

/* header */
.topbar{left:428px;top:0;width:772px;height:40px;background:var(--red);clip-path:polygon(0 0,100% 0,100% 100%,24px 100%)}
.topbar-mail{left:714px;top:9px;color:#fff;font-size:15px;display:flex;align-items:center;gap:10px}
.topbar-phone{left:907px;top:0;width:181px;height:40px;background:var(--navy);color:#fff;font-size:14px;display:flex;align-items:center;justify-content:center;gap:9px}
.brand{left:112px;top:6px;width:142px;height:104px;display:flex;flex-direction:column;align-items:center;justify-content:center;gap:6px;background:#fff;border-radius:0 0 50% 50%/0 0 30% 30%;z-index:5}
.brand-dot{width:38px;height:38px;border-radius:50%;background:var(--red)}
.brand-name{font-weight:800;font-size:21px;color:var(--navy);letter-spacing:.5px}
.nav{left:684px;top:58px;display:flex;gap:33px;font-size:15px;color:#222}
.nav .on{color:var(--red);font-weight:500}

/* hero */
.hero{left:0;top:94px;width:1200px;height:636px;overflow:hidden}
.hero-photo{position:absolute;inset:0;background:linear-gradient(120deg,#a9c48a 0%,#7fa35e 35%,#8fb2d4 55%,#b5874f 75%,#4f7a3a 100%)}
.hero-veil{position:absolute;inset:0;background:rgba(255,255,255,.72);clip-path:polygon(0 0,670px 0,533px 100%,0 100%)}
.hero-title{left:113px;top:238px;font-weight:700;font-size:50px;line-height:66px;color:#33323a}
.hero-title .mark{background:var(--red);color:#fff;padding:0 6px 2px 12px;margin-left:-12px}
.hero-sub{left:114px;top:446px;font-size:25px;line-height:33px;color:#2e2e36}
.btn{display:inline-flex;align-items:center;justify-content:center;background:var(--red);color:#fff;font-weight:700;font-size:15px;letter-spacing:.4px;border-radius:3px}
.hero-btn{left:115px;top:536px;width:147px;height:46px}
.dots{display:flex;gap:7px;align-items:center}
.dots i{width:11px;height:11px;border-radius:50%;border:1.5px solid #777;display:block}
.dots i.on{width:16px;height:16px;border:none;background:var(--red)}
.hero-dots{left:115px;top:693px}

/* section headings */
.sc-title{font-weight:700;font-variant:small-caps;color:var(--navy);font-size:38px;letter-spacing:.3px}
.rule{width:48px;height:4px;background:var(--red)}

/* about */
.dot-field{left:52px;top:1118px;width:330px;height:220px;background-image:radial-gradient(#111 1.8px,transparent 2.2px);background-size:18px 18px;clip-path:polygon(0 0,12% 0,12% 82%,100% 82%,100% 100%,0 100%)}
.about-frame{left:102px;top:831px;width:483px;height:458px;border:5px solid var(--navy);border-radius:5px;background:#fff;padding:4px}
.about-photo{width:100%;height:100%;background:linear-gradient(160deg,#8fb6e0 0%,#9b6b4a 35%,#2f5fd0 60%,#d52c2c 78%,#5e9b3c 100%)}
.about-title{left:617px;top:845px}
.about-rule{left:617px;top:900px}
.about-text{left:617px;top:913px;width:488px;font-size:17.5px;line-height:27px;color:var(--muted)}
.about-btn{left:617px;top:1210px;width:145px;height:46px}

/* stats */
.stats-band{left:0;top:1419px;width:1200px;height:288px;background:var(--red-band)}
.pink-zone{left:0;top:1707px;width:1200px;height:987px;background:var(--pink)}
.stats-title{left:0;top:1490px;width:1200px;text-align:center;color:#fff;font-size:33px}
.stats-rule{left:576px;top:1544px;background:#fff}
.stat{top:1596px;width:236px;height:222px;background:#fff;border:2px solid #8c5b4e;border-radius:5px;text-align:center}
.stat b{display:block;margin-top:34px;font-size:82px;line-height:88px;font-weight:700;color:var(--navy)}
.stat span{display:block;margin-top:14px;font-size:23px;line-height:26px;font-weight:500;color:#222}

/* gallery */
.gallery-title{left:0;top:1890px;width:1200px;text-align:center}
.gallery-rule{left:576px;top:1942px}
.shot{border-radius:4px}
.g-a{left:0;top:1959px;width:141px;height:219px;background:linear-gradient(160deg,#7aa0d6,#a88a6a 60%,#5f9a3a)}
.g-b{left:0;top:2200px;width:141px;height:290px;background:linear-gradient(160deg,#6f9ee0,#8a97a8 55%,#4d8a32)}
.g-c{left:158px;top:2018px;width:438px;height:396px;background:linear-gradient(170deg,#8ab6e6 0%,#c9d4dc 35%,#7d8694 60%,#4c9030 100%)}
.g-d{left:614px;top:2070px;width:439px;height:396px;background:linear-gradient(170deg,#9cc2ea 0%,#eceff2 40%,#a9744a 62%,#4d8d32 100%)}
.g-e{left:1069px;top:1959px;width:131px;height:219px;background:linear-gradient(160deg,#9ac0e8,#c7b596 55%,#5a9a38)}
.g-f{left:1069px;top:2200px;width:131px;height:290px;background:linear-gradient(160deg,#b8d0ea,#e9e9ea 50%,#578f35)}
.arrow{top:2544px;width:52px;height:52px;border:2px solid var(--navy);border-radius:50%;display:flex;align-items:center;justify-content:center}

/* reviews */
.reviews-title{left:0;top:2762px;width:1200px;text-align:center}
.reviews-rule{left:576px;top:2816px}
.review{top:2849px;width:264px;border:1.5px solid var(--line);border-radius:5px;background:#fff;padding:20px 14px 0 17px}
.stars{display:flex;gap:6px}
.review h3{margin-top:16px;font-size:20px;line-height:25px;font-weight:600;color:#1e1e26}
.review p{margin-top:12px;font-size:14.5px;line-height:23px;color:var(--muted)}
.person{display:flex;align-items:center;gap:10px;margin-top:28px;padding-bottom:20px}
.avatar{width:40px;height:40px;border-radius:50%}
.person b{display:block;font-size:16px;font-weight:600;color:#222;line-height:19px}
.person small{display:block;font-size:13px;color:#555}
.review-dots{left:563px;top:3253px}

/* footer */
.footer{left:0;top:3357px;width:1200px;height:354px;background:var(--navy-deep);color:#fff}
.f-brand{left:220px;top:3430px;width:127px;display:flex;flex-direction:column;align-items:center;gap:8px}
.f-brand .brand-dot{width:44px;height:44px;background:#fff}
.f-brand .brand-name{color:#fff;font-size:21px}
.social{top:3551px;width:33px;height:33px;border:1.5px solid #fff;border-radius:50%}
.f-col{top:3412px}
.f-col h4{font-size:21px;font-weight:600}
.f-col .rule{width:52px;height:2px;background:#8c93bd;margin:10px 0 12px}
.f-col li{list-style:none;font-size:13px;line-height:26px;color:#e8eaf4}
.f-divider{left:111px;top:3623px;width:978px;height:1px;background:#4c568e}
.f-copy{left:116px;top:3652px;font-size:14px;color:#dfe2f0}
.f-legal{left:862px;top:3652px;font-size:14px;color:#dfe2f0;display:flex;gap:22px}
</style>
</head>
<body>

<!-- header -->
<div class="abs topbar"></div>
<div class="abs topbar-mail">
  <svg width="22" height="15" viewBox="0 0 22 15"><rect x="1" y="1" width="20" height="13" fill="none" stroke="#fff" stroke-width="1.6"/><path d="M1 1l10 7 10-7" fill="none" stroke="#fff" stroke-width="1.6"/></svg>
  info@tovandex4.com
</div>
<div class="abs topbar-phone">
  <svg width="17" height="17" viewBox="0 0 24 24"><path fill="#fff" d="M6.6 10.8a15.1 15.1 0 006.6 6.6l2.2-2.2a1 1 0 011-.25 11.4 11.4 0 003.6.57 1 1 0 011 1V20a1 1 0 01-1 1A17 17 0 013 4a1 1 0 011-1h3.5a1 1 0 011 1c0 1.25.2 2.45.57 3.57a1 1 0 01-.25 1z"/></svg>
  +1 (888) 555-0142
</div>
<div class="abs brand"><span class="brand-dot"></span><span class="brand-name">TOVANDEX4</span></div>
<nav class="abs nav">
  <a class="on" href="#">★ Home</a><a href="#">About</a><a href="#">Services</a><a href="#">Projects</a><a href="#">Careers</a>
</nav>

<!-- hero -->
<section class="abs hero">
  <div class="hero-photo" role="img" aria-label="Suburban American home with a flag on the porch, green lawn and hedges"></div>
  <div class="hero-veil"></div>
</section>
<h1 class="abs hero-title"><span class="mark">Engineering Today</span> to<br>Ensure a Better<br>Tomorrow.</h1>
<p class="abs hero-sub">Perspiciatis unde omnis iste natus<br>error sitvoluptatem accusantium</p>
<a class="abs btn hero-btn" href="#">CONTACT US</a>
<div class="abs dots hero-dots"><i></i><i class="on"></i><i></i><i></i></div>

<!-- about -->
<div class="abs dot-field"></div>
<div class="abs about-frame"><div class="about-photo" role="img" aria-label="House with patriotic bunting and red, white and blue flower garden"></div></div>
<h2 class="abs sc-title about-title">About Us</h2>
<div class="abs rule about-rule"></div>
<p class="abs about-text">Karspiciatis unde omnis iste natus error sisaeset voluptatem accusantium doloremque laudantium, totam rem aperiam, eaque ipsa quae ab illo inventore veritatis eset qusaeseseasi architecto beatae vitae dicta sunt explicabo. Nemo esesnim ipsam voluptatem quia voluptas sit aspernatur asaut odseit aut fugit, sed quia consequuntur magni dolores eoses qsaui ratione voluptatem sequi nesciunt. Neque porro quisquam est, qui dolorem ipsum quia dolor sit amet, consesaesctetur, adipisci velit, sed quia non numquam eius modi temsepora incidunt ut labore et dolore magnam.</p>
<a class="abs btn about-btn" href="#">LEARN MORE</a>

<!-- stats -->
<div class="abs stats-band"></div>
<div class="abs pink-zone"></div>
<h2 class="abs sc-title stats-title" style="color:#fff">Proven Leadership. Quality Engineering.</h2>
<div class="abs rule stats-rule"></div>
<div class="abs stat" style="left:111px"><b>41</b><span>Years in Business</span></div>
<div class="abs stat" style="left:359px"><b>97%</b><span>Repeat Business</span></div>
<div class="abs stat" style="left:606px"><b>30%</b><span>Professional<br>Certifications</span></div>
<div class="abs stat" style="left:854px"><b>94%</b><span>Business Strategic</span></div>

<!-- gallery -->
<h2 class="abs sc-title gallery-title">Project Gallery</h2>
<div class="abs rule gallery-rule"></div>
<div class="abs shot g-a" role="img" aria-label="Blue-sided house with garage"></div>
<div class="abs shot g-b" role="img" aria-label="Gabled family home under blue sky"></div>
<div class="abs shot g-c" role="img" aria-label="Grey shingle house with double garage and lawn"></div>
<div class="abs shot g-d" role="img" aria-label="Modern white and timber residence with garage"></div>
<div class="abs shot g-e" role="img" aria-label="Two-storey suburban home at dusk"></div>
<div class="abs shot g-f" role="img" aria-label="White house framed by bare trees"></div>
<div class="abs arrow" style="left:539px"><svg width="16" height="16" viewBox="0 0 16 16"><path d="M10 2L4 8l6 6" fill="none" stroke="#1a2363" stroke-width="2.4"/></svg></div>
<div class="abs arrow" style="left:608px"><svg width="16" height="16" viewBox="0 0 16 16"><path d="M6 2l6 6-6 6" fill="none" stroke="#1a2363" stroke-width="2.4"/></svg></div>

<!-- reviews -->
<h2 class="abs sc-title reviews-title">Client Reviews</h2>
<div class="abs rule reviews-rule"></div>

<svg width="0" height="0" style="position:absolute"><defs><symbol id="star" viewBox="0 0 20 20"><path d="M10 1l2.7 5.9 6.3.7-4.7 4.3 1.3 6.3L10 15l-5.6 3.2 1.3-6.3L1 7.6l6.3-.7z" fill="#3fae9a"/></symbol></defs></svg>

<article class="abs review" style="left:36px;height:271px">
  <div class="stars"><svg width="18" height="18"><use href="#star"/></svg><svg width="18" height="18"><use href="#star"/></svg><svg width="18" height="18"><use href="#star"/></svg><svg width="18" height="18"><use href="#star"/></svg><svg width="18" height="18"><use href="#star"/></svg></div>
  <h3>Volup tatem accus antiu lasei saeioasei camsei</h3>
  <p>Consectetur adipiscing elitsed do eiusmod tempor incididun.</p>
  <div class="person"><span class="avatar" style="background:#3a9ad9" role="img" aria-label="Client portrait"></span><div><b>Mara Ellison</b><small>CEO &amp; Founder</small></div></div>
</article>
<article class="abs review" style="left:324px;height:321px">
  <div class="stars"><svg width="18" height="18"><use href="#star"/></svg><svg width="18" height="18"><use href="#star"/></svg><svg width="18" height="18"><use href="#star"/></svg><svg width="18" height="18"><use href="#star"/></svg><svg width="18" height="18"><use href="#star"/></svg></div>
  <h3>Volup tatem accus antiu lasei saeioasei camsei</h3>
  <p>Consectetur adipiscing elit, sed do eiusmod tempor incididunt ut labore et dolore magna.</p>
  <div class="person"><span class="avatar" style="background:#f0b23a" role="img" aria-label="Client portrait"></span><div><b>Mara Ellison</b><small>CEO &amp; Founder</small></div></div>
</article>
<article class="abs review" style="left:612px;height:375px">
  <div class="stars"><svg width="18" height="18"><use href="#star"/></svg><svg width="18" height="18"><use href="#star"/></svg><svg width="18" height="18"><use href="#star"/></svg><svg width="18" height="18"><use href="#star"/></svg><svg width="18" height="18"><use href="#star"/></svg></div>
  <h3>Volup tatem accus antiu lasei saeioasei camsei</h3>
  <p>Hansectetur adipiscing elit, sed do eiusmod tempor incididunt ut labore et dolore magna aliqua. Ut enim aliquip ex ea commodo consequ.</p>
  <div class="person" style="margin-top:44px"><span class="avatar" style="background:#8d3fa8" role="img" aria-label="Client portrait"></span><div><b>Mara Ellison</b><small>CEO &amp; Founder</small></div></div>
</article>
<article class="abs review" style="left:900px;height:271px">
  <div class="stars"><svg width="18" height="18"><use href="#star"/></svg><svg width="18" height="18"><use href="#star"/></svg><svg width="18" height="18"><use href="#star"/></svg><svg width="18" height="18"><use href="#star"/></svg><svg width="18" height="18"><use href="#star"/></svg></div>
  <h3>Volup tatem accus antiu lasei saeioasei camsei</h3>
  <p>Consectetur adipiscing elitsed do eiusmod tempor incididun.</p>
  <div class="person"><span class="avatar" style="background:#e0453a" role="img" aria-label="Client portrait"></span><div><b>Mara Ellison</b><small>CEO &amp; Founder</small></div></div>
</article>
<div class="abs dots review-dots"><i></i><i class="on"></i><i></i><i></i></div>

<!-- footer -->
<footer class="abs footer"></footer>
<div class="abs f-brand"><span class="brand-dot"></span><span class="brand-name">TOVANDEX4</span></div>
<span class="abs social" style="left:246px" aria-label="Social profile"></span>
<span class="abs social" style="left:291px" aria-label="Social profile"></span>
<div class="abs f-col" style="left:465px"><h4>Quick Links</h4><div class="rule"></div><ul><li>Home</li><li>About</li><li>Services</li><li>Projects</li><li>Careers</li></ul></div>
<div class="abs f-col" style="left:677px"><h4>Links</h4><div class="rule"></div><ul><li>Copyright</li><li>Legal</li><li>Privacy</li><li>Accessibility</li><li>Sitemap</li></ul></div>
<div class="abs f-col" style="left:880px"><h4>Support</h4><div class="rule"></div><ul><li>Team</li><li>About Us</li><li>Careers</li><li>Our Values</li></ul></div>
<div class="abs f-divider"></div>
<div class="abs f-copy">©2024. All rights reserved.</div>
<div class="abs f-legal"><span>Privacy</span><span>|</span><span>Terms &amp; Conditions</span></div>

</body>
</html>
```